PillPeak website blog. Simple medical advice given in clear yes or no answers that save people money

I am developing a new web page that provides medical care cost savings at the consumers' fingertips. I need a web page that is clean, concise, and attractive for me to put my valuable medical information on. The information I provide is simple to obtain, yet very valuable to the consumer, and answered in a yes or no format. For example, A person may wonder if they need an antibiotic for cold like symptoms. Seeing a doctor for an antibiotic is very expensive. But with simple and clear advice at their fingertips, they can confidently avoid having to pay $200 or more to see a doctor and get an antibiotic. This is kind of like consumer reports for medical services.

Target Market(s)

People who are savvy shoppers and want to save money on healthcare. Likely younger ages between 21 and 60, who are mobile, readily use iphones, and want strong evidence based research to guide their decisions.

Industry/Entity Type

Coding

Number of Pages Required

Colors

Requirements
Must have
• A template on the "Question" and "Answer" page that can be edited many times that can be edited many times. The Confidence rating scale would need to be edited as well. The "Date Researched" the "PillPeak Pilluminate" and "References" all need to be able to be edited. This website must be very clear and simple to understand. A medical question is posed with a yes or no answer, then answered and given a confidence rating, we then tell them how much money they saved by going to our website.
Nice to have
• We want this to be slightly fun, vibrant, warm and inviting. This will be sometime later converted into an app format. Quirky, some humor to keep it interesting.
Should not have
• No sterile looking medical images. Not boring.

```html
<!DOCTYPE html>
<html lang="en">
<head>
<meta charset="utf-8">
<title>PillPeak</title>
<link href="https://fonts.googleapis.com/css2?family=Montserrat:wght@500;600;700&family=Fredoka:wght@500;600&display=swap" rel="stylesheet">
<style>
:root{
  --blue:#1474bf;
  --red:#e3232a;
  --ink:#1d1d1d;
  --grey-tab:#a3a3a3;
  --footer:#3c3c3c;
  --line:#e2e2e2;
  --white:#ffffff;
}
*{box-sizing:border-box;margin:0;padding:0}
html,body{width:1200px;height:1033px;overflow:hidden;background:var(--white);font-family:"Montserrat",sans-serif;color:var(--ink)}
.page{position:relative;width:1200px;height:1033px}
.brand{position:absolute;left:111px;top:58px;display:flex;align-items:center;gap:12px}
.brand-dot{width:34px;height:34px;border-radius:50%;background:var(--blue)}
.brand-name{font-family:"Fredoka",sans-serif;font-weight:600;font-size:40px;color:var(--blue)}
.search{position:absolute;left:386px;top:51px;width:305px;height:43px;border:2px solid #d8d8d8;border-radius:22px;display:flex;align-items:center}
.search span{padding-left:16px;font-size:13.5px;color:#666;flex:1}
.search b{width:111px;height:43px;margin:-2px -2px -2px 0;background:var(--blue);color:var(--white);border-radius:22px;display:flex;align-items:center;justify-content:center;font-weight:500;font-size:14.5px}
.banner{position:absolute;left:660px;top:0;width:540px;height:134px}
.banner-text{position:absolute;left:700px;top:36px;width:440px;text-align:center;color:var(--white);font-family:"Fredoka",sans-serif;font-weight:600;font-size:24px;letter-spacing:1.6px;line-height:31px}
.rule{position:absolute;left:111px;top:159px;width:978px;height:2px;background:var(--line)}
.nav{position:absolute;left:111px;top:180px;width:978px;display:flex;justify-content:space-between;font-weight:600;font-size:15.5px}
.hero{position:absolute;left:0;top:219px;width:1200px;height:559px;background:linear-gradient(100deg,#8a8683 0%,#7b726d 30%,#5b6f8a 60%,#2f6fb5 78%,#6d7f95 100%)}
.tabs{position:absolute;left:0;top:321px;width:289px}
.tab{height:54px;margin-bottom:6px;background:var(--white);border-radius:0 27px 27px 0;display:flex;align-items:center;font-weight:500;font-size:16.5px}
.tab i{width:44px;height:44px;margin:0 16px 0 4px;display:flex;align-items:center;justify-content:center}
.tab .b{background:var(--blue)} .tab .r{background:var(--red)}
.hero-copy{position:absolute;left:334px;top:345px;width:300px;text-align:center;color:var(--white);font-family:"Fredoka",sans-serif;font-weight:600;font-size:36px;line-height:49.5px}
.hero-btn{position:absolute;left:414px;top:569px;width:141px;height:44px;border:2px solid var(--white);border-radius:22px;color:var(--white);font-size:16.5px;font-weight:500;display:flex;align-items:center;justify-content:center}
.dots{position:absolute;left:455px;top:643px;display:flex;gap:4px}
.dots span{width:17px;height:17px;border-radius:50%;background:#c9c9c9}
.dots span:first-child{background:var(--white)}
.join{position:absolute;left:377px;top:782px;width:446px;height:66px}
.join-text{position:absolute;left:377px;top:797px;width:446px;text-align:center;color:var(--white);font-family:"Fredoka",sans-serif;font-weight:500;font-size:25.5px}
.email{position:absolute;left:291px;top:874px;width:493px;height:43px;border:2px solid #d4d4d4;border-radius:22px;padding-left:16px;display:flex;align-items:center;font-size:14px;color:#555}
.submit{position:absolute;left:793px;top:874px;width:117px;height:43px;background:var(--blue);border-radius:22px;color:var(--white);font-weight:600;font-size:15.5px;display:flex;align-items:center;justify-content:center}
.footer{position:absolute;left:0;top:958px;width:1200px;height:75px;background:var(--footer);color:var(--white);font-weight:500;font-size:15px}
.footer .left{position:absolute;left:111px;top:14px;line-height:28px}
.footer .right{position:absolute;right:110px;top:12px;text-align:right;font-family:"Fredoka",sans-serif;font-weight:500;font-size:18.5px;line-height:28px}
.footer .right u{text-decoration:underline}
</style>
</head>
<body>
<div class="page">
  <div class="brand"><span class="brand-dot"></span><span class="brand-name">PillPeak</span></div>
  <div class="search"><span>Search Here...</span><b>Search</b></div>

  <svg class="banner" viewBox="0 0 540 134" aria-hidden="true">
    <path d="M8 0 Q60 20 64 80 Q68 132 120 132 L540 132 L540 0 Z" fill="var(--red)"/>
    <path d="M12 0 Q56 22 60 80 Q64 128 120 128 L540 128 L540 0 Z" fill="var(--blue)"/>
  </svg>
  <div class="banner-text">CLEAR. VALUABLE. HEALTH.<br>ADVICE. RIGHT NOW.</div>

  <div class="rule"></div>
  <nav class="nav">
    <span>Prev / Screening</span><span>Women's Health</span><span>Men's Health</span><span>Meds</span><span>Surgery</span><span>Imaging</span><span>Peds</span><span>Contact Us</span>
  </nav>

  <div class="hero" role="img" aria-label="Photo of a doctor in blue scrubs touching a ring of health-service icons"></div>

  <div class="tabs">
    <div class="tab"><i class="b"><svg width="22" height="22" viewBox="0 0 22 22"><circle cx="11" cy="11" r="9" fill="none" stroke="#fff" stroke-width="2"/><text x="11" y="16" text-anchor="middle" fill="#fff" font-size="13" font-weight="700" font-family="Montserrat">?</text></svg></i>Who Are We?</div>
    <div class="tab"><i class="r"><svg width="22" height="22" viewBox="0 0 22 22" fill="none" stroke="#fff" stroke-width="2"><path d="M3 8l8-4 8 4-8 4z"/><path d="M3 12l8 4 8-4M3 16l8 4 8-4"/></svg></i>How It Works?</div>
    <div class="tab"><i class="b"><svg width="24" height="22" viewBox="0 0 24 22" fill="none" stroke="#fff" stroke-width="1.8"><path d="M2 4h8l2 2 2-2h8v14h-8l-2 2-2-2H2z"/><path d="M12 6v14"/></svg></i>Evidence Based Research</div>
    <div class="tab"><i class="r"><svg width="22" height="24" viewBox="0 0 22 24" fill="#fff"><circle cx="11" cy="7" r="5"/><path d="M2 23c0-6 4-9 9-9s9 3 9 9z"/></svg></i>Dr. Whitfield</div>
    <div class="tab"><i class="b"><svg width="22" height="24" viewBox="0 0 22 24" fill="#fff"><circle cx="11" cy="7" r="5"/><path d="M2 23c0-6 4-9 9-9s9 3 9 9z"/></svg></i>Who We Are Not</div>
    <div class="tab"><i class="r"><svg width="24" height="22" viewBox="0 0 24 22" fill="none" stroke="#fff" stroke-width="1.8"><path d="M12 2v18M6 20h12M3 5h18"/><path d="M3 5l-2 7h6zM21 5l-2 7h6z"/></svg></i>Are We Biased?</div>
  </div>

  <div class="hero-copy">Save $1,000 per<br>Year On<br>Healthcare.<br>It’s Free!</div>
  <div class="hero-btn">Click Here!</div>
  <div class="dots"><span></span><span></span><span></span></div>

  <svg class="join" viewBox="0 0 446 66" aria-hidden="true">
    <path d="M0 0 H446 Q412 4 408 34 Q404 66 370 66 H76 Q42 66 38 34 Q34 4 0 0 Z" fill="var(--grey-tab)"/>
  </svg>
  <div class="join-text">Become A PillPeak Today!</div>

  <div class="email">Enter Email</div>
  <div class="submit">Submit</div>

  <footer class="footer">
    <div class="left">Copyrights © 2018 PillPeak. All Rights Reserved.<br>Disclaimer: Nemo enim ipsam voluptatem quia voluptas quae ab illo inventore</div>
    <div class="right">Ask a question here!<br><u>If it is worthy, Well post it!</u></div>
  </footer>
</div>
</body>
</html>
```